MRT Property - Business Cards

Looking for a business card & general letterhead, signage etc design for our new logo.

Colours:
000a20
0056a2
00b5ef
0088ce
68cef2

Fonts:
Poppins
Karla

Please keep look and feel of new brand - example in the zip package I sent.

```html
<!DOCTYPE html>
<html lang="en">
<head>
<meta charset="utf-8">
<title>MRT Property – Business Cards</title>
<link rel="stylesheet" href="https://fonts.googleapis.com/css2?family=Poppins:wght@400;600&family=Delius&family=Montserrat:wght@400;500&display=swap">
<style>
  :root {
    --ink-navy: #000a20;
    --brand-blue: #0056a2;
    --brand-deep: #0d55a6;
    --brand-mid: #0088ce;
    --brand-cyan: #00b5ef;
    --brand-sky: #68cef2;
    --text-blue: #0d4a9c;
    --text-dark: #222a35;
    --paper: #ffffff;
    --backdrop: #e9ebee;
  }
  * { margin: 0; padding: 0; box-sizing: border-box; }
  html, body { width: 900px; height: 1200px; overflow: hidden; }
  body { background: var(--backdrop); position: relative; font-family: "Montserrat", sans-serif; }

  .card {
    position: absolute;
    width: 742px;
    height: 440px;
    border-radius: 22px;
    overflow: hidden;
    box-shadow: 0 6px 16px rgba(0, 10, 32, 0.25);
  }
  .card-front { left: 80px; top: 131px; background: var(--paper); }
  .card-back { left: 79px; top: 638px; background: var(--brand-deep); }

  .front-waves { position: absolute; left: 0; top: 0; width: 742px; height: 440px; }

  .wordmark {
    position: absolute;
    font-family: "Poppins", sans-serif;
    font-weight: 600;
    white-space: nowrap;
    display: flex;
    align-items: center;
    gap: 10px;
    line-height: 1;
  }
  .wordmark-dot { border-radius: 50%; flex: none; }
  .front-wordmark { left: 74px; top: 200px; font-size: 28px; color: var(--brand-blue); }
  .front-wordmark .wordmark-dot { width: 26px; height: 26px; background: var(--brand-cyan); }

  .divider {
    position: absolute;
    left: 348px; top: 97px;
    width: 2px; height: 224px;
    background: var(--brand-blue);
  }

  .contact-block { position: absolute; left: 364px; top: 94px; color: var(--text-dark); }
  .person-name {
    font-family: "Delius", cursive;
    font-size: 30px;
    color: var(--text-blue);
    line-height: 40px;
    font-weight: 400;
  }
  .person-title { font-size: 15px; line-height: 20px; margin-top: 1px; }
  .address { font-size: 15px; line-height: 22px; margin-top: 23px; }
  .contact-list { list-style: none; margin-top: 15px; }
  .contact-list li {
    display: flex; align-items: center; gap: 12px;
    font-size: 15px; line-height: 28px;
  }
  .contact-icon { width: 15px; height: 15px; flex: none; }

  .back-pattern { position: absolute; inset: 0; }
  .back-wordmark { left: 492px; top: 322px; font-size: 24px; color: var(--paper); }
  .back-wordmark .wordmark-dot { width: 22px; height: 22px; background: var(--brand-sky); }
</style>
</head>
<body>

  <section class="card card-front">
    <svg class="front-waves" viewBox="0 0 742 440" aria-hidden="true">
      <path d="M0,322 C170,305 330,340 470,382 C590,415 690,395 742,330 L742,440 L0,440 Z" fill="var(--brand-cyan)"/>
      <path d="M0,340 C170,323 330,356 470,398 C590,428 690,410 742,365" fill="none" stroke="var(--paper)" stroke-width="4"/>
      <path d="M0,347 C170,332 330,362 470,404 C590,434 690,420 742,385 L742,440 L0,440 Z" fill="var(--brand-deep)"/>
      <path d="M400,378 C520,400 640,392 742,330 L742,345 C650,395 540,408 400,378 Z" fill="var(--brand-sky)" opacity="0.8"/>
    </svg>

    <div class="wordmark front-wordmark">
      <span class="wordmark-dot"></span>MRT Property
    </div>

    <div class="divider"></div>

    <div class="contact-block">
      <h1 class="person-name">Daniel Harper</h1>
      <p class="person-title">Mnaging Director</p>
      <p class="address">482 Maple Ridge Ave Suite<br>210 Columbus Ohio 43215</p>
      <ul class="contact-list">
        <li>
          <svg class="contact-icon" viewBox="0 0 16 16" aria-hidden="true"><path d="M4 1.5 L6 4.5 L4.8 6.2 C5.6 8 7.8 10.3 9.8 11.2 L11.5 10 L14.5 12 L13 14.5 C7 14.5 1.5 9 1.5 3 Z" fill="var(--brand-blue)"/></svg>
          1 (555) 204-7319
        </li>
        <li>
          <svg class="contact-icon" viewBox="0 0 16 16" aria-hidden="true"><rect x="1" y="3.5" width="14" height="9" rx="1" fill="var(--brand-blue)"/><path d="M1.5 4.5 L8 9 L14.5 4.5" fill="none" stroke="var(--paper)" stroke-width="1.2"/></svg>
          info@mrtproperty.com
        </li>
        <li>
          <svg class="contact-icon" viewBox="0 0 16 16" aria-hidden="true"><circle cx="8" cy="8" r="7" fill="var(--brand-blue)"/><path d="M1 8 H15 M8 1 C4.5 4.5 4.5 11.5 8 15 M8 1 C11.5 4.5 11.5 11.5 8 15" fill="none" stroke="var(--paper)" stroke-width="1"/></svg>
          www.mrtproperty.com
        </li>
      </ul>
    </div>
  </section>

  <section class="card card-back">
    <svg class="back-pattern" viewBox="0 0 744 440" role="img" aria-label="Repeating brand sail pattern fading from bright cyan at top left into deep blue">
      <defs>
        <linearGradient id="patternFade" x1="0" y1="0" x2="1" y2="0.6">
          <stop offset="0" stop-color="var(--brand-cyan)" stop-opacity="0.75"/>
          <stop offset="0.45" stop-color="var(--brand-mid)" stop-opacity="0.25"/>
          <stop offset="1" stop-color="var(--ink-navy)" stop-opacity="0.18"/>
        </linearGradient>
      </defs>
      <rect width="744" height="440" fill="url(#patternFade)"/>
    </svg>

    <div class="wordmark back-wordmark">
      <span class="wordmark-dot"></span>MRT Property
    </div>
  </section>

</body>
</html>
```